Book Title: “Faith: Road of Endless Grace” Please see the attachment “Text on the cover”.

Book Cover Design Instructions: This book is meant for people of all religions and nationalities. Therefore, on the cover, there should be no mosque or an object specific to any religion. The primary emphasis should be on the "unconditional love of God." Therefore, use universal symbols of love. The second priority themes could be Sufism, Peace, and self-improvement. Rest is your imagination. Please also see the attachment: 'Book description and author's Bio.'
This book has the potential to be a best seller. Please do a good job.
What Book Cover Formats are required: A designer should submit cover designs in three formats: (1) eBook, (2) Paperback, and (3) Hardback. These books will be published on Borvex QPL.
Format requirements for eBooks are available from: https://qpl.borvex.example/en_US/help/topic/R731928457.
You can find paperback and hardback cover measurements from: https://qpl.borvex.example/en_US/cover-calculator
• To complete the project, all three formats should be accepted by Borvex QPL.
• The book interior trim size is 6.14 X 9.21 inches.
• Interior Type: Premium color.
• No bleed.
• I do not upload barcode. So, the back cover should have room for Borvex to print the barcode.
• Number of pages 126.
Compensation for the designer: After selecting one designer, I will increase the amount by $200 on Artvelle to compensate for three deliverables.
Follow-up of the Project:
After the book is published, I may need minor revisions. For example, the number of pages may change. Therefore, I will need the same design in revised sizes. In that case, I will pay $25 for each revision. For example, if the number of pages changes, I will need a different spine for paperback and hardback, then I will pay the artist $25 + $25 = $50 for both designs.
List of Enclosers:
1. Text on the cover.
2. Book description and author's Bio for the back cover.
3. Later, I will upload my picture for the book's back cover.

Target Market(s)

Any adult

Industry/Entity Type

Any industry

Requirements
Must have
• Three Deliverables

```html
<!DOCTYPE html>
<html lang="en">
<head>
<meta charset="utf-8">
<title>Faith: Road of Endless Grace — Cover</title>
<link rel="stylesheet" href="https://fonts.googleapis.com/css2?family=Montserrat:wght@400;500;600&display=swap">
<style>
  :root {
    --page: #ffffff;
    --cover: #332923;
    --gold-dark: #c4952f;
    --gold-mid: #e6c878;
    --gold-light: #fff6c8;
    --ink-light: #ffffff;
    --rule: #b8913a;
  }
  html, body {
    margin: 0;
    padding: 0;
    width: 1200px;
    height: 1200px;
    overflow: hidden;
    background: var(--page);
  }
  .canvas {
    position: relative;
    width: 1200px;
    height: 1200px;
    background: var(--page);
  }
  .cover {
    position: absolute;
    left: 222px;
    top: 31px;
    width: 762px;
    height: 1144px;
    background: var(--cover);
    font-family: "Montserrat", sans-serif;
    color: var(--ink-light);
    text-align: center;
  }
  .cover__title {
    position: absolute;
    left: 0;
    right: 0;
    top: 46px;
    margin: 0;
    font-size: 206px;
    font-weight: 500;
    line-height: 1;
    letter-spacing: -2px;
    background: linear-gradient(100deg, var(--gold-dark) 0%, var(--gold-mid) 45%, var(--gold-light) 100%);
    -webkit-background-clip: text;
    background-clip: text;
    color: transparent;
  }
  .cover__subtitle {
    position: absolute;
    left: 0;
    right: 0;
    top: 256px;
    margin: 0;
    font-size: 46px;
    font-weight: 500;
    line-height: 1;
    letter-spacing: 1px;
  }
  .cover__rule {
    position: absolute;
    left: 104px;
    width: 555px;
    height: 1px;
    background: linear-gradient(90deg, transparent, var(--rule) 15%, var(--gold-mid) 50%, var(--rule) 85%, transparent);
  }
  .cover__rule--top { top: 354px; }
  .cover__rule--bottom { top: 431px; }
  .cover__tagline {
    position: absolute;
    left: 0;
    right: 0;
    top: 362px;
    margin: 0;
    line-height: 1.3;
  }
  .cover__tagline-lead {
    display: block;
    font-size: 24px;
    font-weight: 400;
  }
  .cover__tagline-main {
    display: block;
    font-size: 24px;
    font-weight: 600;
  }
  .cover__artwork {
    position: absolute;
    left: 185px;
    top: 490px;
    width: 393px;
    height: 470px;
  }
  .cover__author {
    position: absolute;
    left: 0;
    right: 0;
    top: 1017px;
    margin: 0;
    font-size: 50px;
    font-weight: 400;
    line-height: 1;
    letter-spacing: 1px;
  }
</style>
</head>
<body>
  <div class="canvas">
    <section class="cover">
      <h1 class="cover__title">FAITH</h1>
      <p class="cover__subtitle">ROAD OF ENDLESS GRACE</p>

      <div class="cover__rule cover__rule--top"></div>
      <p class="cover__tagline">
        <span class="cover__tagline-lead">Guide to</span>
        <span class="cover__tagline-main">Cultivating Inner Peace and Mindful Living</span>
      </p>
      <div class="cover__rule cover__rule--bottom"></div>

      <svg class="cover__artwork" viewBox="0 0 393 470" role="img" aria-label="Gold line illustration of a whirling Sufi dancer in a flowing skirt, one arm raised">
        <defs>
          <radialGradient id="artwork-glow" cx="50%" cy="55%" r="55%">
            <stop offset="0%" stop-color="#e6c878" stop-opacity="0.45"/>
            <stop offset="70%" stop-color="#c4952f" stop-opacity="0.15"/>
            <stop offset="100%" stop-color="#332923" stop-opacity="0"/>
          </radialGradient>
        </defs>
        <ellipse cx="196" cy="250" rx="196" ry="220" fill="url(#artwork-glow)"/>
      </svg>

      <p class="cover__author">DR. NOREEN VALDAR</p>
    </section>
  </div>
</body>
</html>
```